Brell Stone Company Business Cards

Front and Back Business Card - logo and text setup - cool design. I need workable photoshop or illustrator files so I can setup each employee card with design that is created
Updates

Hi everyone, thank you for the great entries. Please no more white and blue cards - there are so many already - black and silver only now please. thanks!

Target Market(s)

Construction Industry - Facility Managers

Industry/Entity Type

Construction

Contact Information for Business Card

I really like contemporary simplistic looks - clean neat....not opposed to seeing some black backrounds

Requirements
Must have
• Logo/website address with design on front only - www.brellstone-example.com (logo attached)
• Back:
• Name/Title/Company Address/Phone/email address
Nice to have
• Cool design
Should not have
• Nothing gimmicky like Fire or Water - since we are a Fire Protection company - it has all been done

```html
<!DOCTYPE html>
<html lang="en">
<head>
<meta charset="utf-8">
<title>Brell Stone Company Business Cards</title>
<link href="https://fonts.googleapis.com/css2?family=Lato:wght@400;700;900&display=swap" rel="stylesheet">
<style>
  :root {
    --stage: #3a3b3e;
    --black: #121213;
    --charcoal: #2b2c2f;
    --silver: #c3c6cb;
    --silver-light: #e7e8ea;
    --silver-dark: #8e9197;
  }
  * { box-sizing: border-box; margin: 0; padding: 0; }
  html, body { width: 1200px; height: 912px; overflow: hidden; background: var(--stage); }
  body { font-family: "Lato", sans-serif; position: relative; }
  .card {
    position: absolute;
    width: 540px; height: 309px;
    top: 301px;
    overflow: hidden;
  }
  .card--front { left: 40px; background: var(--black); }
  .card--back { left: 620px; background: var(--silver-light); }

  .wordmark { font-weight: 900; letter-spacing: -1px; line-height: 1; white-space: nowrap; }
  .card--front .wordmark {
    position: absolute; left: 0; right: 0; top: 112px;
    text-align: center; font-size: 60px; color: var(--silver);
  }
  .card--front .site {
    position: absolute; left: 0; right: 0; top: 226px;
    text-align: center; font-size: 14px; color: var(--silver); letter-spacing: 0.3px;
  }

  .card--back .wordmark {
    position: absolute; left: 34px; top: 56px;
    font-size: 42px; color: var(--black);
  }
  .person { position: absolute; right: 30px; top: 78px; text-align: right; color: var(--black); }
  .person__name { font-size: 22px; font-weight: 700; white-space: nowrap; }
  .person__title { font-size: 12px; margin-top: 2px; color: var(--charcoal); }
  .divider {
    position: absolute; left: 26px; right: 30px; top: 130px;
    height: 1px; background: var(--silver-dark);
  }
  .contact { position: absolute; left: 34px; top: 150px; list-style: none; color: var(--black); font-size: 14px; }
  .contact li { display: flex; align-items: center; gap: 10px; margin-bottom: 6px; white-space: nowrap; }
  .contact svg { width: 14px; height: 14px; color: var(--charcoal); flex: none; }
  .address { position: absolute; right: 30px; top: 150px; text-align: right; font-size: 13px; color: var(--black); line-height: 1.4; }
  .stripe { position: absolute; left: 0; bottom: 0; width: 540px; height: 28px; }
  .stripe__main { fill: var(--black); }
  .stripe__accent { fill: var(--silver-dark); }
</style>
</head>
<body>
  <section class="card card--front" aria-label="Card front">
    <div class="wordmark">Brell Stone</div>
    <div class="site">www.brellstone-example.com</div>
  </section>

  <section class="card card--back" aria-label="Card back">
    <div class="wordmark">Brell Stone</div>
    <div class="person">
      <div class="person__name">Marla Vance Hollis</div>
      <div class="person__title">President</div>
    </div>
    <div class="divider"></div>
    <ul class="contact">
      <li><svg viewBox="0 0 16 16" aria-hidden="true"><path fill="currentColor" d="M3 1l3 3-1.5 2a9 9 0 0 0 5.5 5.5L12 10l3 3-2 2C7 15 1 9 1 3z"/></svg>(555) 014-2290</li>
      <li><svg viewBox="0 0 16 16" aria-hidden="true"><path d="M1 3h14v10H1z M1 3l7 6 7-6" fill="none" stroke="currentColor" stroke-width="1.6"/></svg>info@brellstone-example.com</li>
      <li><svg viewBox="0 0 16 16" aria-hidden="true"><circle cx="8" cy="8" r="7" fill="none" stroke="currentColor" stroke-width="1.4"/><path d="M1 8h14M8 1c-3 4-3 10 0 14M8 1c3 4 3 10 0 14" fill="none" stroke="currentColor" stroke-width="1.2"/></svg>www.brellstone-example.com</li>
    </ul>
    <div class="address">48 Harbor Works Lane<br>Millbrook, NY 10000</div>
    <svg class="stripe" viewBox="0 0 540 28" preserveAspectRatio="none" aria-hidden="true">
      <polygon class="stripe__main" points="0,16 390,16 384,28 0,28"/>
      <polygon class="stripe__accent" points="398,6 540,6 540,28 388,28"/>
    </svg>
  </section>
</body>
</html>
```